Business Card & Letterhead Design

We a financial advice company based in Australia. We provide advice to wealthy farmers.

We are changing our business name FROM Brightvale Financial TO Tallowmere Wealth and we need a new letterhead and double sided business card design

Attached is designs from our previous branding (Brightvale Financial) as it includes all the details we require on the new Tallowmere Wealth business cards and letterhead.

Need extra days to review

```html
<!DOCTYPE html>
<html lang="en">
<head>
<meta charset="utf-8">
<title>Tallowmere Wealth — Stationery</title>
<link rel="stylesheet" href="https://fonts.googleapis.com/css2?family=Poppins:ital,wght@0,400;0,500;0,600;1,400&family=Roboto:wght@300;400&family=Crimson+Text:ital@0;1&display=swap">
<style>
  :root {
    --backdrop: #e4e4e4;
    --paper: #f3f3f3;
    --ink-dark: #3e3e3e;
    --ink-body: #5a5a5a;
    --ink-soft: #6e6e6e;
    --on-dark: #f2f2f2;
    --on-dark-soft: #c9c9c9;
    --mark-faint: rgba(0,0,0,0.045);
  }
  * { box-sizing: border-box; margin: 0; padding: 0; }
  html, body { width: 1200px; height: 1027px; overflow: hidden; }
  body { background: var(--backdrop); position: relative; font-family: "Poppins", sans-serif; }

  /* ---------- Letterhead ---------- */
  .letterhead { position: absolute; left: 486px; top: 97px; width: 580px; height: 820px; background: var(--paper); overflow: hidden; }
  .letterhead-watermark { position: absolute; left: 108px; top: 329px; width: 348px; height: 348px; border-radius: 50%; border: 12px solid var(--mark-faint); }
  .letterhead-header { position: absolute; left: 0; top: 0; width: 100%; height: 123px; background: var(--ink-dark); }
  .header-rule { position: absolute; left: 0; top: 126px; width: 100%; height: 2px; background: var(--ink-dark); }
  .brand { position: absolute; left: 36px; top: 34px; width: 200px; text-align: center; color: var(--on-dark); }
  .brand-dot { width: 44px; height: 44px; margin: 0 auto; border-radius: 50%; border: 2px solid var(--on-dark); }
  .brand-name { font-weight: 400; font-size: 15.5px; letter-spacing: 0.6px; line-height: 1; margin-top: 8px; text-transform: uppercase; }
  .brand-tag { font-size: 5.6px; letter-spacing: 2.4px; margin-top: 3px; color: var(--on-dark-soft); text-transform: uppercase; }
  .header-divider { position: absolute; top: 36px; width: 1px; height: 65px; background: var(--on-dark-soft); }
  .header-col { position: absolute; top: 36px; color: var(--on-dark); font-size: 7.7px; line-height: 9.4px; }

  .letter { position: absolute; left: 56px; top: 0; width: 471px; color: var(--ink-body); font-family: "Roboto", sans-serif; font-weight: 300; }
  .salutation { position: absolute; top: 193px; font-size: 13.4px; font-weight: 400; color: var(--ink-dark); white-space: nowrap; }
  .letter-body { position: absolute; top: 238px; width: 471px; }
  .letter-body p { font-size: 7.9px; line-height: 12.2px; text-align: justify; margin-bottom: 12.4px; }
  .closing { position: absolute; top: 518px; font-size: 8px; }
  .signature { position: absolute; left: 56px; top: 544px; width: 86px; height: 52px; background: linear-gradient(180deg, rgba(40,40,40,0.08), rgba(40,40,40,0.16)); border-radius: 3px; }

  .letterhead-legal { position: absolute; left: 0; top: 747px; width: 100%; text-align: center; font-size: 7.8px; line-height: 9.6px; color: var(--ink-dark); }
  .footer-rule { position: absolute; left: 0; top: 779px; width: 100%; height: 1.5px; background: var(--ink-dark); }
  .letterhead-footer { position: absolute; left: 0; top: 782px; width: 100%; height: 38px; background: var(--ink-dark); text-align: center; color: var(--on-dark); padding-top: 9px; }
  .motto { font-weight: 600; font-size: 8.6px; line-height: 10px; text-transform: uppercase; }
  .motto-sub { font-style: italic; font-size: 8.2px; line-height: 10px; display: flex; justify-content: center; align-items: center; gap: 4px; }
  .motto-sub::before, .motto-sub::after { content: ""; width: 10px; height: 1px; background: currentColor; }

  /* ---------- Business card, front ---------- */
  .card { position: absolute; left: 140px; width: 292px; height: 166px; overflow: hidden; }
  .card-front { top: 543px; background: var(--paper); color: var(--ink-dark); }
  .card-front .watermark { position: absolute; left: 88px; top: 21px; width: 114px; height: 114px; border-radius: 50%; border: 5px solid var(--mark-faint); }
  .card-front .motto-block { position: absolute; top: 32px; width: 100%; text-align: center; }
  .card-front .motto { font-size: 7.6px; line-height: 9px; }
  .card-front .motto-sub { font-size: 6.4px; line-height: 8px; }
  .card-front .motto-sub::before, .card-front .motto-sub::after { width: 12px; background: var(--ink-soft); }
  .person { position: absolute; right: 165px; top: 68px; text-align: right; white-space: nowrap; }
  .person-name { font-weight: 600; font-size: 9.6px; line-height: 11px; }
  .person-creds { font-size: 5.8px; line-height: 7px; font-weight: 500; }
  .person-role { font-size: 5.8px; line-height: 7px; color: var(--ink-soft); }
  .card-divider { position: absolute; left: 136px; top: 66px; width: 1px; height: 41px; background: var(--ink-dark); }
  .contact-list { position: absolute; left: 144px; top: 66px; list-style: none; font-size: 6px; line-height: 8px; color: var(--ink-body); }
  .contact-list li { display: flex; align-items: center; gap: 4px; white-space: nowrap; }
  .contact-list svg { width: 5px; height: 5px; fill: var(--ink-dark); flex: none; }
  .address-list { position: absolute; top: 121px; width: 100%; list-style: none; text-align: center; font-size: 6px; line-height: 9px; color: var(--ink-body); }
  .address-list li { display: flex; justify-content: center; align-items: center; gap: 2px; }
  .address-list svg { width: 5px; height: 6px; fill: var(--ink-dark); }

  /* ---------- Business card, back ---------- */
  .card-back { top: 750px; background: var(--ink-dark); color: var(--on-dark); text-align: center; }
  .card-back .brand-dot { position: absolute; left: 124px; top: 40px; width: 44px; height: 44px; margin: 0; border-color: #2e2e2e; }
  .card-back .brand-name { position: absolute; top: 89px; width: 100%; margin: 0; font-size: 14.6px; color: #8f8f8f; }
  .card-back .brand-tag { position: absolute; top: 106px; width: 100%; margin: 0; font-size: 5.4px; color: #7a7a7a; }
  .services { position: absolute; top: 124px; width: 100%; font-family: "Crimson Text", serif; font-size: 8px; color: var(--on-dark); }
  .licensee { position: absolute; top: 138px; width: 100%; font-family: "Crimson Text", serif; font-style: italic; font-size: 6px; line-height: 8.4px; color: var(--on-dark-soft); }
  .licensee .ruled { display: flex; justify-content: center; align-items: center; gap: 4px; }
  .licensee .ruled::before, .licensee .ruled::after { content: ""; width: 46px; height: 0.6px; background: var(--on-dark-soft); }
</style>
</head>
<body>

<section class="letterhead" aria-label="Letterhead">
  <div class="letterhead-watermark"></div>

  <header class="letterhead-header">
    <div class="brand">
      <div class="brand-dot"></div>
      <div class="brand-name">Tallowmere Wealth</div>
      <div class="brand-tag">Strategic Financial Advice</div>
    </div>
    <div class="header-divider" style="left:236px"></div>
    <div class="header-col" style="left:256px">
      Kestrel Holdings Pty Ltd<br>
      ATF The Marlow Investment<br>
      Trust T/AS Brightvale Financial<br>
      ABN: 51 208 637 192<br>
      Corporate Authorised<br>
      Representative of Summit<br>
      Advice Group Limited
    </div>
    <div class="header-divider" style="left:380px"></div>
    <div class="header-col" style="left:397px">
      Suite 4A, 18 Wattle St<br>
      Riverbend QLD 4000<br>
      PO Box 5120<br>
      Eastfield QLD 4000<br>
      p (07) 5550 1234 f (07) 5550 1299<br>
      admin@brightvalefinancial.com.au<br>
      www.brightvalefinancial.com.au
    </div>
  </header>
  <div class="header-rule"></div>

  <article class="letter">
    <p class="salutation">Dear Mr. Hartley,</p>
    <div class="letter-body">
      <p>Lorem ipsum dolor sit amet, consectetur adipiscing elit. Donec orci purus, luctus vitae dignissim eu, iaculis sed purus. Vivamus faucibus, ipsum nec aliquet viverra, leo mauris condimentum ligula, sit amet sagittis enim ligula quis arcu. Nam egestas tortor id nisi porttitor mattis. In tortor ante, ultricies in suscipit a, tempus non massa. Vivamus et auctor mi. Fusce vel massa nulla. Phasellus nec eros mauris, et scelerisque orci.</p>
      <p>Donec malesuada orci vitae nulla accumsan porta a id massa. Quisque accumsan iaculis magna sit amet fringilla. Maecenas consequat, magna eget tincidunt semper, odio nibh rutrum mi, id feugiat ante nisi eu risus. Vestibulum nunc orci, rhoncus a placerat in, ultricies in mi. Cras mattis varius eros, vel fringilla nisi suscipit eget. Quisque scelerisque sagittis nulla at porttitor.</p>
      <p>Sed id augue vitae urna euismod commodo aliquet a quam. Pellentesque arcu velit, cursus et malesuada ut, consequat et diam. Nullam erat sem, rhoncus id ullamcorper vitae, rhoncus et arcu. In ultricies ultricies nulla, ut rutrum nisi iaculis at. Donec eu magna a metus ornare faucibus. Fusce aliquet faucibus ultricies. Morbi semper, est id tincidunt gravida, sem arcu adipiscing lacus, ac bibendum nulla leo eu purus. Quisque nec diam sed risus consectetur a ccumsan quis quis nibh. Vestibulum id purus lorem.</p>
      <p>It is a long established fact that a reader will be distracted by the readable content of a page when looking at its layout. The point of using Lorem Ipsum is that it has a more-or-less normal distribution of letters, as opposed to using 'Content here, content here', making it look like readable English. Many desktop publishing packages</p>
      <p>ada ut, consequat et diam. Nullam erat sem, rhoncus id ullamcorper vitae, rhoncus et arcu. In ultricies ultricies nulla, ut rutrum nisi iaculis at. Donec eu magna a metus ornare faucibus. Fusce aliquet faucibus ultricies. Morbi semper,</p>
    </div>
    <p class="closing">Sincerely,</p>
  </article>
  <div class="signature" role="img" aria-label="Handwritten signature of Sam Reid"></div>

  <p class="letterhead-legal">
    Summit Advice Group Limited | ABN 62 114 903 557 | Australian Financial Services Licence<br>
    Licence Number 318 402 | Principle Address: 410 Harbour Rd, PO Box 3310 Melbourne VIC 3001
  </p>
  <div class="footer-rule"></div>
  <footer class="letterhead-footer">
    <div class="motto">Financial Peace of Mind</div>
    <div class="motto-sub">A referral built business</div>
  </footer>
</section>

<section class="card card-front" aria-label="Business card front">
  <div class="watermark"></div>
  <div class="motto-block">
    <div class="motto">Financial Peace of Mind</div>
    <div class="motto-sub">A referral built business</div>
  </div>

  <div class="person">
    <div class="person-name">SAM REID</div>
    <div class="person-creds">B.Ag.Ec. Dip F.P. CFP®</div>
    <div class="person-role">Managing Director</div>
    <div class="person-role">Authorised Representative</div>
  </div>
  <div class="card-divider"></div>
  <ul class="contact-list">
    <li><svg viewBox="0 0 10 10"><path d="M2 0.5 L4 2.8 L3 4 Q4.2 6 6 7 L7.2 6 L9.5 8 L8 9.6 Q3.5 9 0.4 2 Z"/></svg>(07) 5550 1234</li>
    <li><svg viewBox="0 0 10 10"><path d="M2.5 0 H7.5 V10 H2.5 Z M3.5 1 V8 H6.5 V1 Z"/></svg>0400 555 218</li>
    <li><svg viewBox="0 0 10 10"><path d="M2.5 0 H7.5 V3 H10 V8 H0 V3 H2.5 Z M3.5 1 V3 H6.5 V1 Z M2 9 H8 V10 H2 Z"/></svg>(07) 5550 1299</li>
    <li><svg viewBox="0 0 10 10"><path d="M0 2 H10 V8 H0 Z M1 3 L5 5.6 L9 3 Z" fill-rule="evenodd"/></svg>sam@brightvalefinancial.com.au</li>
    <li><svg viewBox="0 0 10 10"><circle cx="5" cy="5" r="5"/></svg>www.brightvalefinancial.com.au</li>
  </ul>
  <ul class="address-list">
    <li><svg viewBox="0 0 10 12"><path d="M5 0 A4.5 4.5 0 0 1 9.5 4.5 C9.5 7.5 5 12 5 12 C5 12 0.5 7.5 0.5 4.5 A4.5 4.5 0 0 1 5 0 Z M5 3 A1.5 1.5 0 1 0 5 6 A1.5 1.5 0 1 0 5 3 Z" fill-rule="evenodd"/></svg>Suite 4A, 18 Wattle St, Riverbend QLD 4000</li>
    <li><svg viewBox="0 0 10 12"><path d="M5 0 A4.5 4.5 0 0 1 9.5 4.5 C9.5 7.5 5 12 5 12 C5 12 0.5 7.5 0.5 4.5 A4.5 4.5 0 0 1 5 0 Z M5 3 A1.5 1.5 0 1 0 5 6 A1.5 1.5 0 1 0 5 3 Z" fill-rule="evenodd"/></svg>PO Box 5120, Eastfield QLD 4000</li>
  </ul>
</section>

<section class="card card-back" aria-label="Business card back">
  <div class="brand-dot"></div>
  <div class="brand-name">Tallowmere Wealth</div>
  <div class="brand-tag">Strategic Financial Advice</div>
  <p class="services">Life &amp; TPD Insurance • Income Protection • Financial Planning</p>
  <div class="licensee">
    <div class="ruled">Summit Advice Group limited</div>
    <div>Australian Financial Services licensee License Number 318402</div>
  </div>
</section>

</body>
</html>
```